Letter design, envelope design, and more

Hello, we the Tavrin Gmbh are looking for our shop. Letter C5. Design does not have to be like a business card, so it can have straight lines. Only the color is important. The logo is the text under TaVRin omit.It should not be playful but Profesionel

Font styles to use
Sans Serif

Colors
0555a3
3176b5
85abd2
85cae6
34a7d8
0792cd
cee9f5
cfdfed
000000

Requirements
Must have
• Color like business card, Please, with the text under TaVRin, Correct address Lindmattstr. 4 Zip code 9517 Seewil, as well as Couvert Without addressing only design and logo with TaVrn
Nice to have
• more writing articles
Should not have
• Not too colored, Text under TaVRin, bright colors

```html
<!DOCTYPE html>
<html lang="en">
<head>
<meta charset="utf-8">
<title>Tavrin Gmbh – Letterhead and C5 Envelope</title>
<link rel="stylesheet" href="https://fonts.googleapis.com/css2?family=Arimo:wght@700&family=PT+Sans:wght@400;700&display=swap">
<style>
  :root {
    --stage: #e1e1e1;
    --paper: #ffffff;
    --navy: #24325f;
    --brand-blue: #0555a3;
    --mid-blue: #3176b5;
    --soft-blue: #85abd2;
    --accent-blue: #0792cd;
    --pale-blue: #cfdfed;
    --ink: #2b2b2b;
  }
  * { box-sizing: border-box; margin: 0; padding: 0; }
  html, body { width: 1200px; height: 800px; overflow: hidden; }
  body {
    background: var(--stage);
    position: relative;
    font-family: "PT Sans", sans-serif;
  }

  /* Shared brand mark */
  .brand {
    position: absolute;
    display: flex;
    align-items: center;
    gap: 8px;
  }
  .brand-square {
    width: 30px; height: 30px;
    background: var(--navy);
  }
  .brand-name {
    font-family: "PT Sans", sans-serif;
    font-weight: 700;
    font-size: 22px;
    letter-spacing: 1px;
    color: var(--navy);
    line-height: 1;
  }

  /* Shared contact footer */
  .contact-footer {
    position: absolute;
    left: 0; bottom: 0;
    width: 100%;
    height: 18px;
  }
  .contact-footer > svg { position: absolute; inset: 0; }
  .contact-line {
    position: absolute;
    top: 4px;
    display: flex;
    align-items: center;
    gap: 6px;
    font-size: 7.6px;
    color: #ffffff;
    white-space: nowrap;
  }
  .contact-line span { display: inline-flex; align-items: center; gap: 2px; }
  .contact-line svg { width: 7px; height: 7px; }

  /* Letterhead */
  .letterhead {
    position: absolute;
    left: 81px; top: 86px;
    width: 485px; height: 628px;
    background: var(--paper);
  }
  .letterhead .brand { left: 52px; top: 24px; }
  .header-rule {
    position: absolute;
    top: 77px; left: 0; width: 100%;
    height: 6px;
  }
  .header-rule::before,
  .header-rule::after {
    content: "";
    position: absolute;
    top: 2px; height: 2px;
    background: var(--accent-blue);
  }
  .header-rule::before { left: 0; width: 363px; }
  .header-rule::after { left: 446px; right: 0; }
  .web-address {
    position: absolute;
    left: 370px; top: -1px;
    font-size: 7.6px;
    letter-spacing: 1.6px;
    color: var(--ink);
  }
  .web-address b { font-weight: 400; color: var(--accent-blue); }

  .letter-body {
    position: absolute;
    left: 49px; top: 133px;
    width: 388px;
    color: #3a3a3a;
  }
  .salutation {
    font-family: "Arimo", sans-serif;
    font-weight: 700;
    font-size: 11px;
    line-height: 14px;
    color: #1b1b1b;
    margin-bottom: 13px;
  }
  .letter-body p.copy {
    font-size: 9.7px;
    line-height: 12.4px;
    letter-spacing: -0.1px;
    text-align: justify;
    margin-bottom: 12.4px;
  }
  .signature {
    position: absolute;
    left: 50px; top: 486px;
    width: 74px; height: 34px;
    background: var(--pale-blue);
    opacity: .5;
    border-radius: 4px;
  }
  .letterhead .contact-line { left: 130px; }

  /* C5 envelope */
  .envelope {
    position: absolute;
    left: 606px; top: 286px;
    width: 515px; height: 428px;
  }
  .envelope-flap {
    position: absolute;
    left: 0; top: 0;
    width: 515px; height: 65px;
  }
  .flap-address {
    position: absolute;
    left: 0; width: 100%;
    top: 26px;
    text-align: center;
    font-size: 6.5px;
    letter-spacing: 1.6px;
    color: #ffffff;
    transform: rotate(180deg);
  }
  .envelope-face {
    position: absolute;
    left: 0; top: 64px;
    width: 515px; height: 364px;
    background: var(--paper);
  }
  .envelope .brand { left: 40px; top: 28px; }
  .envelope .contact-line { left: 149px; }
</style>
</head>
<body>

  <!-- Letterhead -->
  <section class="letterhead">
    <div class="brand">
      <div class="brand-square"></div>
      <span class="brand-name">TAVRIN</span>
    </div>

    <div class="header-rule">
      <span class="web-address">www.<b>tavrin</b>.ch</span>
    </div>

    <div class="letter-body">
      <p class="salutation">Dear Mr. Keller,</p>
      <p class="copy">Lorem Ipsum is simply dummy text of the printing and typesetting industry. Lorem Ipsum has been the industry's standard dummy text ever since the 1500s, when an unknown printer took a galley of type and scrambled it to make a type specimen book. It has survived not only five centuries, but also the leap into electronic typesetting, remaining essentially unchanged.</p>
      <p class="copy">The standard chunk of Lorem Ipsum used since the 1500s is reproduced below for those interested. Sections 1.10.32 and 1.10.33 from "de Finibus Bonorum et Malorum" by Cicero are also reproduced in their exact original form, accompanied by English versions from the 1914 translation by H. Rackham</p>
      <p class="copy">Lorem Ipsum is simply dummy text of the printing and typesetting industry. Lorem Ipsum has been the industry's standard dummy text ever since the 1500s, when an unknown printer took a galley of type and scrambled it to make a type specimen book. It has survived not only five centuries, but also the leap into electronic typesetting, remaining essentially unchanged. It was popularised in the</p>
      <p class="copy">The standard chunk of Lorem Ipsum used since the 1500s is reproduced below for those interested. Sections 1.10.32 and 1.10.33 from "de Finibus Bonorum et Malorum" by Cicero are also reproduced in their exact original form, accompanied by English versions from the 1914 translation by H. Rackham</p>
      <p class="copy">The standard chunk of Lorem Ipsum used since the 1500s is reproduced below for those interested. Sections 1.10.32 and 1.10.33 from "de Finibus Bonorum et Malorum" by Cicero are</p>
    </div>

    <div class="signature" role="img" aria-label="Handwritten signature of the sender"></div>

    <footer class="contact-footer">
      <svg width="485" height="18" viewBox="0 0 485 18" aria-hidden="true">
        <rect x="0" y="0" width="485" height="5" fill="var(--soft-blue)"/>
        <rect x="0" y="10" width="485" height="8" fill="var(--mid-blue)"/>
        <path d="M112 18 C118 18 118 1 126 1 L376 1 C384 1 384 18 390 18 Z" fill="var(--mid-blue)"/>
      </svg>
      <div class="contact-line">
        <span><svg viewBox="0 0 10 10"><circle cx="5" cy="5" r="4.2" fill="none" stroke="#fff" stroke-width="1"/><path d="M3.5 3 L4.5 3 L5 4.3 L4.4 4.8 Q5 6 6.2 6.6 L6.7 6 L8 6.5 L8 7.4 Q5 7.6 3.5 3 Z" fill="#fff"/></svg>+41 71 555 02 40</span>
        <span><svg viewBox="0 0 10 10"><rect x="1" y="2.5" width="8" height="5.5" fill="none" stroke="#fff" stroke-width="1"/><path d="M1 2.5 L5 5.8 L9 2.5" fill="none" stroke="#fff" stroke-width="1"/></svg>info@tavrin.ch</span>
        <span><svg viewBox="0 0 10 10"><path d="M5 9.5 C3 6.5 2 5 2 3.6 A3 3 0 0 1 8 3.6 C8 5 7 6.5 5 9.5 Z" fill="#fff"/><circle cx="5" cy="3.7" r="1.1" fill="var(--mid-blue)"/></svg>Lindmattstr. 4 &nbsp;9517 Seewil,</span>
      </div>
    </footer>
  </section>

  <!-- C5 envelope -->
  <section class="envelope">
    <svg class="envelope-flap" width="515" height="65" viewBox="0 0 515 65" aria-hidden="true">
      <path d="M4 65 L4 26 C4 14 12 12 26 10 C180 -3 335 -3 490 10 C504 12 511 15 511 26 L515 65 Z" fill="var(--soft-blue)"/>
    </svg>
    <div class="flap-address">www.tavrin.ch</div>

    <div class="envelope-face">
      <div class="brand">
        <div class="brand-square"></div>
        <span class="brand-name">TAVRIN</span>
      </div>

      <footer class="contact-footer">
        <svg width="515" height="18" viewBox="0 0 515 18" aria-hidden="true">
          <rect x="0" y="0" width="515" height="5" fill="var(--soft-blue)"/>
          <rect x="0" y="10" width="515" height="8" fill="var(--mid-blue)"/>
          <path d="M118 18 C124 18 124 1 132 1 L390 1 C398 1 398 18 404 18 Z" fill="var(--mid-blue)"/>
        </svg>
        <div class="contact-line">
          <span><svg viewBox="0 0 10 10"><circle cx="5" cy="5" r="4.2" fill="none" stroke="#fff" stroke-width="1"/><path d="M3.5 3 L4.5 3 L5 4.3 L4.4 4.8 Q5 6 6.2 6.6 L6.7 6 L8 6.5 L8 7.4 Q5 7.6 3.5 3 Z" fill="#fff"/></svg>+41 71 555 02 40</span>
          <span><svg viewBox="0 0 10 10"><rect x="1" y="2.5" width="8" height="5.5" fill="none" stroke="#fff" stroke-width="1"/><path d="M1 2.5 L5 5.8 L9 2.5" fill="none" stroke="#fff" stroke-width="1"/></svg>info@tavrin.ch</span>
          <span><svg viewBox="0 0 10 10"><path d="M5 9.5 C3 6.5 2 5 2 3.6 A3 3 0 0 1 8 3.6 C8 5 7 6.5 5 9.5 Z" fill="#fff"/><circle cx="5" cy="3.7" r="1.1" fill="var(--mid-blue)"/></svg>Lindmattstr. 4 &nbsp;9517 Seewil,</span>
        </div>
      </footer>
    </div>
  </section>

</body>
</html>
```